Executive Business Card for Healthcare Company [Need Today]

I need a business card design for a healthcare company. The only branding the company has thus far is a logo. The cards will be utilized by company executives. The design I envision will be vibrant and appealing but with a corporate feel. They shouldn't be too casual or playful. I would like to complete this project TODAY if possible.

Target Market(s)

Healthcare vendors, other executives in healthcare and pharmaceuticals

Industry/Entity Type

Pharmaceutical

Contact Information for Business Card

See attachment

Font styles to use
Serif
Sans Serif

Colors

Designer to choose colors to be used in the design.

```html
<!DOCTYPE html>
<html lang="en">
<head>
<meta charset="utf-8">
<title>Corvane Therapeutics – Executive Business Card</title>
<link href="https://fonts.googleapis.com/css2?family=Roboto:wght@300;400;500&display=swap" rel="stylesheet">
<style>
  :root {
    --backdrop: #e8e8ea;
    --teal-top: #25b1c1;
    --teal-bottom: #4db592;
    --teal-ink: #2aa6b8;
    --paper: #fbfbfb;
    --ink: #4a4a4a;
    --ink-soft: #777;
    --white: #ffffff;
  }
  * { box-sizing: border-box; margin: 0; padding: 0; }
  html, body { width: 1200px; height: 726px; overflow: hidden; }
  body {
    background: var(--backdrop);
    font-family: 'Roboto', Arial, sans-serif;
    position: relative;
  }
  .card {
    position: absolute;
    top: 208px;
    width: 540px;
    height: 310px;
    border-radius: 3px;
    box-shadow: 0 8px 22px rgba(0,0,0,.12);
    overflow: hidden;
  }
  /* Front */
  .card-front {
    left: 40px;
    background: linear-gradient(170deg, var(--teal-top) 0%, var(--teal-bottom) 100%);
    color: var(--white);
  }
  .front-brand {
    position: absolute;
    left: 0; right: 0; top: 112px;
    display: flex; align-items: center; justify-content: center; gap: 18px;
  }
  .brand-dot {
    width: 62px; height: 62px;
    border: 2px solid var(--white);
    border-radius: 50%;
  }
  .front-brand .brand-name {
    font-size: 34px; font-weight: 300; letter-spacing: 1px;
  }
  .front-web {
    position: absolute; bottom: 44px; left: 0; right: 0;
    text-align: center; font-size: 14px; font-weight: 300; letter-spacing: 5px;
  }
  /* Back */
  .card-back {
    left: 620px;
    background: var(--paper);
  }
  .back-brand {
    position: absolute; left: 34px; top: 118px; width: 210px;
    display: flex; flex-direction: column; align-items: center; gap: 14px;
    color: var(--teal-ink);
  }
  .back-brand .brand-dot { border-color: var(--teal-ink); width: 66px; height: 66px; }
  .back-brand .brand-name { font-size: 22px; font-weight: 400; text-align: center; line-height: 1.2; }
  .contact {
    position: absolute; left: 290px; top: 56px;
  }
  .contact-name { font-size: 22px; font-weight: 500; color: var(--teal-ink); }
  .contact-title { font-size: 10px; color: var(--ink-soft); margin-top: 4px; }
  .contact-list { list-style: none; margin-top: 26px; font-size: 13px; color: var(--ink); line-height: 19px; }
  .contact-list li { display: flex; align-items: center; gap: 8px; }
  .contact-list svg { width: 12px; height: 12px; fill: var(--ink-soft); flex: none; }
  .contact-list .indent { padding-left: 20px; }
</style>
</head>
<body>
  <section class="card card-front">
    <div class="front-brand">
      <span class="brand-dot"></span>
      <span class="brand-name">Corvane Therapeutics</span>
    </div>
    <p class="front-web">www.corvanerx.com</p>
  </section>

  <section class="card card-back">
    <div class="back-brand">
      <span class="brand-dot"></span>
      <span class="brand-name">Corvane Therapeutics</span>
    </div>
    <div class="contact">
      <h1 class="contact-name">Daniel Harlow</h1>
      <p class="contact-title">Senior Director of Marketing</p>
      <ul class="contact-list">
        <li><svg viewBox="0 0 12 12"><path d="M2 1h3l1 3-1.5 1a6 6 0 0 0 2.5 2.5L8 6l3 1v3c0 .6-.4 1-1 1A9 9 0 0 1 1 2c0-.6.4-1 1-1z"/></svg>555-201-4830</li>
        <li><svg viewBox="0 0 12 12"><path d="M3 0h6c.6 0 1 .4 1 1v10c0 .6-.4 1-1 1H3c-.6 0-1-.4-1-1V1c0-.6.4-1 1-1zm0 2v7h6V2z"/></svg>555-374-6192</li>
        <li><svg viewBox="0 0 12 12"><path d="M6 0a6 6 0 1 0 0 12A6 6 0 0 0 6 0zm0 1.2c.8 0 1.6 2 1.7 4.2H4.3C4.4 3.2 5.2 1.2 6 1.2zm-1.7 5.4h3.4C7.6 8.8 6.8 10.8 6 10.8S4.4 8.8 4.3 6.6zM1.2 5.4A4.8 4.8 0 0 1 3.6 1.8c-.3.9-.5 2.2-.5 3.6zm0 1.2h1.9c0 1.4.2 2.7.5 3.6a4.8 4.8 0 0 1-2.4-3.6zm7.7 0h1.9a4.8 4.8 0 0 1-2.4 3.6c.3-.9.5-2.2.5-3.6zm0-1.2c0-1.4-.2-2.7-.5-3.6a4.8 4.8 0 0 1 2.4 3.6z"/></svg>dharlow@corvanerx.com</li>
        <li class="indent">118 Linden Park Avenue</li>
        <li class="indent">Fairview, GA 30199</li>
      </ul>
    </div>
  </section>
</body>
</html>
```